Australian Web Design company needs a business card design

We need a business card design for a Sydney based Web Design/Development company called "Blue Fern Web Design". We design, build and deploy websites for small to medium sized businesses. The final design should be clean and communicate that we are a professional and supportive company.
I'd like the Icon to be abstract. Something that embodies the power of the internet, needs to be clean/professional and show that we are human and that we support our customers. Hope that helps.
Target Market(s)
All small to medium businesses
Industry/Entity Type
Business
Contact Information for Business Card
Martin Colby
Blue Fern Web Design
17 Wattle Bend Road
West Barrington
NSW 2317
0427 563 904
martin@bluefernwebstudio.com.au
www.bluefernwebstudio.com.au
Look and feel

```html
<!DOCTYPE html>
<html lang="en">
<head>
<meta charset="utf-8">
<title>Blue Fern Web Design – Business Card</title>
<link rel="stylesheet" href="https://fonts.googleapis.com/css2?family=Roboto:wght@400;700&display=swap">
<style>
  :root {
    --brand-red: #e3232a;
    --ink-navy: #1c2230;
    --silver-light: #ffffff;
    --silver-dark: #c4c4c6;
    --carbon: #1d1d1f;
    --carbon-light: #2e2e31;
    --paper: #ffffff;
    --soft-white: #f3ece8;
  }
  * { box-sizing: border-box; margin: 0; padding: 0; }
  html, body {
    width: 1200px; height: 800px; overflow: hidden;
    background: var(--paper);
    font-family: "Roboto", Arial, sans-serif;
  }
  .canvas { position: relative; width: 1200px; height: 800px; }

  .card {
    position: absolute; top: 110px;
    width: 520px; height: 300px;
    border-radius: 14px; overflow: hidden;
    box-shadow: 0 6px 18px rgba(0,0,0,.18);
  }

  /* Front */
  .card--front {
    left: 50px;
    background: radial-gradient(circle at 62% 55%, var(--silver-light) 0%, #e6e6e7 40%, var(--silver-dark) 100%);
  }
  .front__mark {
    position: absolute; right: -60px; top: -140px;
    width: 260px; height: 260px; border-radius: 50%;
    background: var(--brand-red);
  }
  .brand {
    position: absolute; display: flex; align-items: center; gap: 10px;
    font-weight: 700; color: var(--brand-red); white-space: nowrap;
  }
  .brand__dot { border-radius: 50%; background: var(--brand-red); flex: none; }
  .card--front .brand { left: 26px; top: 34px; font-size: 17px; }
  .card--front .brand__dot { width: 30px; height: 30px; }
  .front__rule {
    position: absolute; left: 0; top: 132px; width: 190px; height: 2px;
    background: var(--brand-red);
  }
  .front__divider {
    position: absolute; left: 190px; top: 132px; width: 2px; height: 146px;
    background: var(--brand-red);
  }
  .contact { position: absolute; left: 206px; top: 142px; color: var(--brand-red); }
  .contact__name { font-size: 25px; font-weight: 400; margin-bottom: 12px; letter-spacing: -.2px; white-space: nowrap; }
  .contact__row { display: flex; align-items: center; gap: 8px; font-size: 12.5px; line-height: 22px; white-space: nowrap; }
  .contact__icon { width: 13px; height: 13px; flex: none; fill: var(--brand-red); }

  /* Back */
  .card--back {
    left: 630px;
    background: linear-gradient(160deg, var(--carbon-light) 0%, var(--carbon) 60%, #151516 100%);
  }
  .back__url {
    position: absolute; left: 0; right: 0; top: 70px; text-align: center;
    color: var(--soft-white); font-size: 12px; letter-spacing: 5px;
  }
  .card--back .brand { left: 50%; top: 140px; transform: translateX(-50%); font-size: 27px; }
  .card--back .brand__dot { width: 46px; height: 46px; }

  /* Standalone logo */
  .logo-lockup { right: 70px; bottom: 90px; font-size: 36px; gap: 16px; }
  .logo-lockup .brand__dot { width: 76px; height: 76px; }
</style>
</head>
<body>
<main class="canvas">

  <section class="card card--front" aria-label="Business card front">
    <div class="front__mark" aria-hidden="true"></div>
    <div class="brand"><span class="brand__dot"></span>Blue Fern Web Design</div>
    <div class="front__rule" aria-hidden="true"></div>
    <div class="front__divider" aria-hidden="true"></div>
    <div class="contact">
      <p class="contact__name">Martin Colby</p>
      <p class="contact__row">
        <svg class="contact__icon" viewBox="0 0 24 24" aria-hidden="true"><path d="M12 2a7 7 0 0 0-7 7c0 5 7 13 7 13s7-8 7-13a7 7 0 0 0-7-7zm0 9.5A2.5 2.5 0 1 1 12 6.5a2.5 2.5 0 0 1 0 5z"/></svg>
        17 Wattle Bend Road West Barrington NSW 2317
      </p>
      <p class="contact__row">
        <svg class="contact__icon" viewBox="0 0 24 24" aria-hidden="true"><path d="M6.6 10.8a15 15 0 0 0 6.6 6.6l2.2-2.2a1 1 0 0 1 1-.25 11.4 11.4 0 0 0 3.6.6 1 1 0 0 1 1 1V20a1 1 0 0 1-1 1A17 17 0 0 1 3 4a1 1 0 0 1 1-1h3.5a1 1 0 0 1 1 1c0 1.250.2 2.450.6 3.6a1 1 0 0 1-.25 1z"/></svg>
        0427 563 904
      </p>
      <p class="contact__row">
        <svg class="contact__icon" viewBox="0 0 24 24" aria-hidden="true"><path d="M12 2a10 10 0 1 0 0 20 10 10 0 0 0 0-20zm6.9 6h-2.9a15.6 15.6 0 0 0-1.4-3.6A8 8 0 0 1 18.9 8zM12 4a14 14 0 0 1 1.9 4h-3.8A14 14 0 0 1 12 4zM4.3 14a8 8 0 0 1 0-4h3.4a16 16 0 0 0 0 4zm.8 2h2.9a15.6 15.6 0 0 0 1.4 3.6A8 8 0 0 1 5.1 16zM8 8H5.1a8 8 0 0 1 4.3-3.6A15.6 15.6 0 0 0 8 8zm4 12a14 14 0 0 1-1.9-4h3.8A14 14 0 0 1 12 20zm2.3-6H9.7a14.7 14.7 0 0 1 0-4h4.6a14.7 14.7 0 0 1 0 4zm.3 5.6a15.6 15.6 0 0 0 1.4-3.6h2.9a8 8 0 0 1-4.3 3.6zM16.3 14a16 16 0 0 0 0-4h3.4a8 8 0 0 1 0 4z"/></svg>
        martin@bluefernwebstudio.com.au
      </p>
    </div>
  </section>

  <section class="card card--back" aria-label="Business card back">
    <p class="back__url">WWW.BLUEFERNWEBSTUDIO.COM.AU</p>
    <div class="brand"><span class="brand__dot"></span>Blue Fern Web Design</div>
  </section>

  <div class="brand logo-lockup"><span class="brand__dot"></span>Blue Fern Web Design</div>

</main>
</body>
</html>
```